Business card for my new company (Accounting firm)

I need a business card for my new business Brightwell Advisory and Ledger SA. Our services are accounting, tax, audit and financial management. Our customers are small companies, start-ups and new companies. The final design has to show financial security, trust and growth. Please find our logo attached to the business card. Text for the business card: Brightwell Advisory and Ledger SA Tomas Varenholt Director and Founder Certified Accountant Tel. 022 418 57 34 tv@clairevalconseil.ch www.clairevalconseil.ch Rue des Vergières 27 1201 Geneva
Target Market(s)
Our customers are small companies, start-ups and new companies.
Industry/Entity Type
Finance And Accounting
Contact Information for Business Card
Claireval Conseil et Comptes SA
Tomas Varenholt
Directeur et Fondateur
Expert-comptable diplômé
Tél. 022 418 57 34
tv@clairevalconseil.ch
www.clairevalconseil.ch
Rue des Vergières 27
1201 Genève

```html
<!DOCTYPE html>
<html lang="fr">
<head>
<meta charset="utf-8">
<title>Claireval Conseil et Comptes – Carte de visite</title>
<link href="https://fonts.googleapis.com/css2?family=Roboto:wght@400;500;700&display=swap" rel="stylesheet">
<style>
  :root {
    --board: #222020;
    --paper: #ffffff;
    --ink: #454545;
    --ink-dark: #3d3d3d;
    --rule: #9a9a9a;
    --blue-deep: #1a6591;
    --blue-sky: #32b1e2;
    --blue-mid: #2a8fcc;
    --white: #ffffff;
  }
  * { margin: 0; padding: 0; box-sizing: border-box; }
  html, body {
    width: 1125px; height: 1200px; overflow: hidden;
    background: var(--board);
    font-family: "Roboto", Arial, sans-serif;
  }
  .card {
    position: absolute; left: 171px; width: 826px; height: 472px;
    box-shadow: 0 3px 8px rgba(0,0,0,.55);
    overflow: hidden;
  }
  .card-front { top: 106px; background: var(--paper); }
  .card-back { top: 639px; background: var(--blue-deep); }

  .brand {
    position: absolute; right: 54px; top: 190px; text-align: right;
    color: var(--ink-dark); font-weight: 500;
  }
  .brand-name { font-size: 46px; letter-spacing: 2px; line-height: 1; }
  .brand-tagline { font-size: 13px; letter-spacing: 2.4px; margin-top: 8px; }
  .brand-mark {
    position: absolute; right: 54px; top: 118px;
    width: 44px; height: 44px; border-radius: 50%; background: var(--blue-sky);
  }

  .person { position: absolute; left: 42px; top: 236px; }
  .person-name { font-size: 29px; font-weight: 700; color: var(--blue-sky); line-height: 1.2; }
  .person-role { font-size: 18px; color: var(--ink); line-height: 24px; }

  .divider {
    position: absolute; left: 42px; top: 342px; width: 730px; height: 2px; background: var(--rule);
  }

  .contacts { position: absolute; left: 46px; top: 358px; list-style: none; }
  .contacts li {
    display: flex; align-items: center; gap: 8px;
    font-size: 19px; color: var(--ink); line-height: 25px;
  }
  .contacts svg { width: 14px; height: 14px; fill: var(--blue-sky); flex: none; }

  .address {
    position: absolute; right: 54px; top: 360px; text-align: right;
    font-size: 19px; color: var(--ink); line-height: 25px;
  }

  .tabs { position: absolute; left: 0; bottom: 0; width: 100%; height: 13px; }
  .tab { position: absolute; bottom: 0; height: 13px; border-radius: 13px 13px 0 0; }
  .tab-deep { left: 0; width: 277px; background: var(--blue-deep); }
  .tab-sky { left: 277px; width: 273px; background: var(--blue-sky); }
  .tab-mid { left: 550px; width: 276px; background: var(--blue-mid); }

  .back-brand {
    position: absolute; left: 0; width: 100%; top: 150px; text-align: center;
    color: var(--white); font-weight: 500;
  }
  .back-brand-name { font-size: 64px; letter-spacing: 3px; line-height: 1; }
  .back-brand-tagline { font-size: 17px; letter-spacing: 3px; margin-top: 12px; }
  .back-url {
    position: absolute; left: 0; width: 100%; top: 402px; text-align: center;
    color: var(--white); font-size: 19px; letter-spacing: 4px;
  }
</style>
</head>
<body>
  <section class="card card-front">
    <span class="brand-mark"></span>
    <div class="brand">
      <div class="brand-name">CLAIREVAL</div>
      <div class="brand-tagline">CONSEIL ET COMPTES</div>
    </div>

    <div class="person">
      <h1 class="person-name">Tomas Varenholt</h1>
      <p class="person-role">Directeur et Fondateur</p>
      <p class="person-role">Expert-comptable diplômé</p>
    </div>

    <div class="divider"></div>

    <ul class="contacts">
      <li>
        <svg viewBox="0 0 24 24" aria-hidden="true"><path d="M6.6 10.8a15.1 15.1 0 0 0 6.6 6.6l2.2-2.2c.3-.3.7-.4 1-.2 1.1.4 2.3.6 3.6.6.6 0 1 .4 1 1V20c0 .6-.4 1-1 1A17 17 0 0 1 3 4c0-.6.4-1 1-1h3.5c.6 0 1 .4 1 1 0 1.3.2 2.5.6 3.6.1.3 0 .7-.2 1z"/></svg>
        022 418 57 34
      </li>
      <li>
        <svg viewBox="0 0 24 24" aria-hidden="true"><path d="M2 5h20v14H2z M2 6l10 7 10-7" /></svg>
        tv@clairevalconseil.ch
      </li>
      <li>
        <svg viewBox="0 0 24 24" aria-hidden="true"><circle cx="12" cy="12" r="10"/></svg>
        www.clairevalconseil.ch
      </li>
    </ul>

    <address class="address" style="font-style:normal">
      Rue des Vergières 27<br>1201 Genève
    </address>

    <div class="tabs">
      <span class="tab tab-deep"></span>
      <span class="tab tab-sky"></span>
      <span class="tab tab-mid"></span>
    </div>
  </section>

  <section class="card card-back">
    <div class="back-brand">
      <div class="back-brand-name">CLAIREVAL</div>
      <div class="back-brand-tagline">CONSEIL ET COMPTES</div>
    </div>
    <p class="back-url">www.clairevalconseil.ch</p>
  </section>
</body>
</html>
```